Brellwick Partners, LLC Stationary

Brellwick Partners, LLC is a new financial planning and consulting company. We are looking for designs on business cards, letterhead, envelopes, and anything else that would be useful. Our preference for business card design is two sided. We are looking for a professional and clean look with incorporating the logo and patriotic feel. Thank you to all who participate and good luck!

```html
<!DOCTYPE html>
<html lang="en">
<head>
<meta charset="utf-8">
<title>Brellwick Partners, LLC Stationery</title>
<link rel="stylesheet" href="https://fonts.googleapis.com/css2?family=Montserrat:wght@400;500;600&display=swap">
<style>
  :root {
    --navy: #1f4a73;
    --navy-deep: #0e3760;
    --red: #b02a30;
    --paper: #f5f5f4;
    --backdrop: #e8e8e8;
    --ink: #5a5a5a;
  }
  * { margin: 0; padding: 0; box-sizing: border-box; }
  html, body { width: 1200px; height: 821px; overflow: hidden; }
  body {
    background: var(--backdrop);
    font-family: "Montserrat", Arial, sans-serif;
    position: relative;
  }
  .sheet {
    position: absolute;
    background: var(--paper);
    box-shadow: 0 2px 6px rgba(0,0,0,0.12);
    overflow: hidden;
  }
  .brand {
    position: absolute;
    display: flex;
    align-items: center;
    gap: 7px;
    color: var(--navy);
    font-weight: 600;
  }
  .brand-dot {
    width: 14px; height: 14px;
    background: var(--navy);
    border-radius: 50%;
    flex: none;
  }
  .brand-block { display: flex; flex-direction: column; }
  .brand-name { font-size: 15px; letter-spacing: 0.3px; line-height: 1.1; }
  .brand-tagline { font-size: 4.6px; letter-spacing: 0.8px; text-transform: uppercase; color: var(--navy); font-weight: 600; margin-top: 2px; }

  /* Letterhead */
  .letterhead { left: 69px; top: 110px; width: 467px; height: 661px; }
  .letterhead .brand { left: 28px; top: 50px; }
  .contact {
    position: absolute;
    left: 352px; top: 26px;
    font-size: 7.2px;
    color: var(--ink);
    line-height: 10px;
  }
  .contact .address { margin-bottom: 5px; }
  .contact .row { display: flex; align-items: center; gap: 4px; margin-bottom: 1.5px; }
  .contact svg { width: 7px; height: 7px; fill: var(--navy); }
  .band {
    position: absolute;
    left: 0; right: 0;
    display: flex;
  }
  .band-navy { background: var(--navy); color: #fff; display: flex; align-items: center; }
  .band-red { background: var(--red); flex: 1; }
  .letterhead .band { bottom: 9px; height: 16px; }
  .letterhead .band-navy { width: 359px; justify-content: center; font-size: 6.8px; letter-spacing: 2px; padding-left: 20px; }

  /* Envelope front */
  .envelope-front { left: 613px; top: 224px; width: 523px; height: 250px; }
  .envelope-front .brand { left: 24px; top: 30px; }
  .envelope-front .band { bottom: 7px; height: 16px; }
  .envelope-front .band-navy { width: 387px; padding-left: 21px; font-size: 7.4px; }

  /* Envelope back */
  .envelope-back { left: 619px; top: 512px; width: 523px; height: 250px; }
  .flap { position: absolute; left: 0; top: 0; width: 523px; height: 92px; }
  .flap-name {
    position: absolute;
    left: 0; right: 0; top: 36px;
    text-align: center;
    color: #fff;
    font-weight: 600;
    font-size: 14px;
    letter-spacing: 0.3px;
  }
</style>
</head>
<body>

  <section class="sheet letterhead" aria-label="Letterhead">
    <div class="brand">
      <span class="brand-dot"></span>
      <div class="brand-block">
        <span class="brand-name">Brellwick Partners, LLC</span>
        <span class="brand-tagline">Financial planning and consulting</span>
      </div>
    </div>
    <div class="contact">
      <p class="address">4120 Larkspur Road<br>Fairbanks, Alaska 34810</p>
      <p class="row"><svg viewBox="0 0 10 10"><path d="M2 0.5l1.8 2.2-1 1.2c.6 1.3 1.6 2.3 2.9 2.9l1.2-1 2.2 1.8-1.2 1.8C4.6 9 1 5.4.7 1.7z"/></svg>555 214 7730</p>
      <p class="row"><svg viewBox="0 0 10 10"><rect x="2.5" y="0.5" width="5" height="3"/><rect x="0.5" y="3.8" width="9" height="4" rx="0.8"/><rect x="2.5" y="7" width="5" height="2.5"/></svg>555 214 7731</p>
      <p class="row"><svg viewBox="0 0 10 10"><rect x="0.5" y="2" width="9" height="6.5"/><path d="M0.5 2l4.5 3.5L9.5 2" fill="none" stroke="#fff" stroke-width="0.9"/></svg>hello@brellwick.com</p>
    </div>
    <div class="band">
      <span class="band-navy">www.brellwick.com</span>
      <span class="band-red"></span>
    </div>
  </section>

  <section class="sheet envelope-front" aria-label="Envelope front">
    <div class="brand">
      <span class="brand-dot"></span>
      <div class="brand-block">
        <span class="brand-name">Brellwick Partners, LLC</span>
        <span class="brand-tagline">Financial planning and consulting</span>
      </div>
    </div>
    <div class="band">
      <span class="band-navy">4120 Larkspur Road, Fairbanks, Alaska 34810</span>
      <span class="band-red"></span>
    </div>
  </section>

  <section class="sheet envelope-back" aria-label="Envelope back">
    <svg class="flap" viewBox="0 0 523 92" aria-hidden="true">
      <path d="M0 0H523L513 80Q511 90 500 90H23Q12 90 10 80Z" fill="var(--navy-deep)"/>
    </svg>
    <p class="flap-name">Brellwick Partners, LLC</p>
  </section>

</body>
</html>
```